Dew and Willow med spa needs an awesome eye catching billboard ad

We need a billboard ad design for a Med Spa with location sin Davenport and Windermere FL A medical spa where the beauty of nature meets the power of science to treat the whole person, mind, body and soul.

Marigold Radiance Med Spa is a medical spa where the beauty of nature meets the power of science to create gorgeous, youthful looking skin. Located in Davenport, Florida, but also serving Four Corners, Celebration, and Windermere, Florida, the talented professional team brings decades of experience in world-class skin care to provide holistic, science-backed aesthetic services and health coaching.

Industry/Entity Type

Spa

Colors
fbee3e
fece3e
eea4c8
e667a6
fbee3d

Requirements
Must have
• Locations in Davenport and Dr Phillips
Phone 407-555-0148
website www.dewandwillow-example.com

Boards for each:
Aesthetic Treatments
Cosmetic Injectables
Quoria facial
add color vs too many earthtones, to catch the eye perhaps using yellow, something that catches the eye and stands out from the normal everyday
Thank you!!!!
Nice to have
• Boards for each:
Aesthetic Treatments
Cosmetic Injectables
Quoria facial
add color vs too many earthtones, to catch the eye
photos that match services,
Thank you!!!!

```html
<!DOCTYPE html>
<html lang="en">
<head>
<meta charset="utf-8">
<title>Marigold Radiance Med Spa – Quoria Facial Billboard</title>
<link rel="stylesheet" href="https://fonts.googleapis.com/css2?family=Cinzel:wght@400;700&family=Marcellus&family=Montserrat:wght@500;600&display=swap">
<style>
  :root {
    --backdrop: #eceef1;
    --board-white: #f8f8f9;
    --gold: #c9ad78;
    --pink-strong: #f3a3cb;
    --pink-soft: #f9d3e5;
    --sun: #fbee3e;
    --sun-deep: #fece3e;
    --ink: #4a4a4c;
    --water: #d9ecf2;
  }
  * { margin: 0; padding: 0; box-sizing: border-box; }
  html, body {
    width: 1143px;
    height: 1200px;
    overflow: hidden;
    background: var(--backdrop);
  }
  .canvas {
    position: relative;
    width: 1143px;
    height: 1200px;
  }
  .billboard {
    position: absolute;
    left: 20px;
    top: 460px;
    width: 1103px;
    height: 280px;
    background: var(--board-white);
    overflow: hidden;
    box-shadow: 0 2px 10px rgba(0,0,0,0.08);
  }
  .flower {
    position: absolute;
    border-radius: 50%;
    background: radial-gradient(circle, var(--pink-strong) 0%, var(--pink-soft) 60%, rgba(249,211,229,0) 75%);
  }
  .flower--top-left { left: -40px; top: -50px; width: 170px; height: 170px; }
  .flower--bottom-left { left: 0; top: 222px; width: 85px; height: 85px; }
  .flower--top-right { right: -40px; top: -30px; width: 200px; height: 220px; }

  .brand {
    position: absolute;
    left: 188px;
    top: 30px;
    display: flex;
    align-items: center;
    gap: 16px;
  }
  .brand__dot {
    width: 58px;
    height: 58px;
    border-radius: 50%;
    background: var(--sun-deep);
    flex: none;
  }
  .brand__name {
    font-family: "Cinzel", serif;
    font-weight: 400;
    font-size: 32px;
    line-height: 1.2;
    letter-spacing: 0.16em;
    color: var(--gold);
  }

  .locations {
    position: absolute;
    left: 262px;
    top: 128px;
    display: flex;
    align-items: center;
    gap: 10px;
    padding: 5px 16px;
    border-radius: 16px;
    background: var(--sun);
    font-family: "Montserrat", sans-serif;
    font-weight: 600;
    font-size: 14px;
    letter-spacing: 0.14em;
    text-transform: uppercase;
    color: var(--ink);
    white-space: nowrap;
  }
  .locations__sep {
    width: 6px;
    height: 6px;
    border-radius: 50%;
    background: var(--ink);
  }

  .service-band {
    position: absolute;
    left: 0;
    top: 172px;
    width: 780px;
    height: 48px;
    background: linear-gradient(90deg, var(--pink-strong) 0%, var(--pink-soft) 55%, rgba(249,211,229,0) 100%);
    border-bottom: 4px solid var(--sun-deep);
  }
  .service-band__title {
    position: absolute;
    left: 262px;
    top: 0;
    line-height: 44px;
    font-family: "Cinzel", serif;
    font-weight: 700;
    font-size: 36px;
    letter-spacing: 0.06em;
    color: var(--ink);
    white-space: nowrap;
  }

  .contact {
    position: absolute;
    left: 140px;
    top: 228px;
    display: flex;
    align-items: center;
    gap: 12px;
    color: var(--ink);
    white-space: nowrap;
  }
  .contact__web {
    font-family: "Cinzel", serif;
    font-size: 17px;
    letter-spacing: 0.02em;
  }
  .contact__divider {
    width: 2px;
    height: 38px;
    background: var(--ink);
  }
  .contact__phone {
    font-family: "Marcellus", serif;
    font-size: 36px;
  }

  .hero-photo {
    position: absolute;
    left: 800px;
    top: 0;
    width: 303px;
    height: 280px;
    background: linear-gradient(100deg, rgba(217,236,242,0) 0%, var(--water) 30%, #cfd9df 60%, rgba(249,211,229,0.5) 100%);
  }
</style>
</head>
<body>
<main class="canvas">
  <section class="billboard" aria-label="Quoria facial billboard">
    <div class="flower flower--top-left" role="img" aria-label="Soft pink flower decoration"></div>
    <div class="flower flower--bottom-left" role="img" aria-label="Small pink flower decoration"></div>

    <div class="brand">
      <span class="brand__dot"></span>
      <span class="brand__name">Marigold Radiance<br>Med Spa</span>
    </div>

    <p class="locations">
      <span>Davenport</span>
      <span class="locations__sep"></span>
      <span>Dr Phillips</span>
    </p>

    <div class="service-band">
      <h1 class="service-band__title">QUORIA FACIAL</h1>
    </div>

    <div class="contact">
      <span class="contact__web">WWW.DEWANDWILLOW-EXAMPLE.COM</span>
      <span class="contact__divider"></span>
      <span class="contact__phone">407-555-0148</span>
    </div>

    <div class="hero-photo" role="img" aria-label="Photo of a woman with glowing skin surrounded by a splash of water"></div>
    <div class="flower flower--top-right" role="img" aria-label="Large pink flower decoration"></div>
  </section>
</main>
</body>
</html>
```